Webdesign for large cottage directory

We have developed a first version of a website that can accommodate large groups (10 to 300 people). The site is English and is aimed at a wide audience ranging from a group of students to a family or a family. For the visitors the site is free and it is the propietaires who pay to see their accommodation. The site is online with just a few fake lodgings and a simple design to the elements that must be appraised (nothing to keep the current design). Our website is here: 9lodgia.com (login / pass = admin / 123) Home page (9lodgia.com): on this page section) and lodging by theme (third section). These three points should be highlighted as possible. The displayed map may be slightly modified. Only the background and the color changes when hovering over the mouse. It can be enlarged / retreciated. Below these 3 sections we have some fairly published articles, the latest blog posts and the footer. The menu will be visible throughout the site. Category page (https://9lodgia.fr/gite-departement/aveyron OR https://9lodgia.fr/gites-couchages-121): On these pages we always return the same format with the googlemap, an image 1 text. Below the list of the cottages concerned and the filter options. Product page: The pages presenting the cottages can be of two types: - Either the cottage has no owner and there is no contact for the visitor to the owner that he can retrieve his cottage by registering: example of a page of this type: https://9lodgia.fr/domaine-de-vercasse - The cottage to a propietaire and we are on the classic card. : // 9lodgia. en / domain-of-vercasse2 For all products on the site we have nav tab. It's just for testing. We do not want to be in the design for real website. All information must be in the page without login / register page: classic, it's here: https://9lodgia.it/login and https://9lodgia.fr/register Blog homepage (https://9lodgia.fr/blog ): Classic blog page Blog post (https://9lodgia.fr/blog/urltemporaire1551521154) and static page (https://9lodgia.fr/blog/Systeme-classement-9lodgiafr): Nothing special Menu: Menu is an important part of the website. It's the way to navigate on the wbesite.
Faible participation designers
4 page

```html
<!DOCTYPE html>
<html lang="fr">
<head>
<meta charset="utf-8">
<title>9lodgia.Fr – Connexion</title>
<link href="https://fonts.googleapis.com/css2?family=Montserrat:wght@400;500;700&family=Roboto+Condensed:wght@400;500;700&family=Roboto:wght@500;700&display=swap" rel="stylesheet">
<style>
:root{
  --navy:#0d3a6b;
  --navy-deep:#0a2f57;
  --panel:#174374;
  --orange:#f7941d;
  --green:#2aa84a;
  --card:#eef0fb;
  --link:#2a8ccf;
  --ink:#1b1b1b;
  --white:#ffffff;
}
*{box-sizing:border-box;margin:0;padding:0}
html,body{width:994px;height:1200px;overflow:hidden;background:var(--white)}
body{position:relative;font-family:"Montserrat",sans-serif;color:var(--ink)}
.abs{position:absolute}

/* top bar */
.topbar{left:593px;top:0;width:401px;height:34px;background:var(--navy);clip-path:polygon(0 0,100% 0,100% 100%,16px 100%)}
.topbar-item{top:8px;color:var(--white);font:500 12.5px "Roboto",sans-serif;display:flex;align-items:center;gap:6px}
.ring{width:18px;height:18px;border:1.5px solid var(--white);border-radius:50%;display:flex;align-items:center;justify-content:center}
.social-dot{top:8px;width:18px;height:18px;border:1.5px solid var(--white);border-radius:50%}

/* header */
.brand{left:17px;top:19px;display:flex;align-items:center;gap:12px}
.brand-mark{width:52px;height:52px;border:3px solid var(--orange)}
.brand-name{font:700 30px "Roboto",sans-serif;color:var(--navy);letter-spacing:.5px}
.account{top:58px;font:500 12.5px "Roboto",sans-serif;color:var(--ink);display:flex;align-items:center;gap:6px}
.sep{top:58px;width:1px;height:16px;background:#ccc}

/* nav */
.nav{left:0;top:96px;width:994px;height:38px;background:var(--navy)}
.nav-item{top:107px;color:var(--white);font:500 14px "Roboto Condensed",sans-serif;display:flex;align-items:center;gap:5px}
.nav-item.active{color:var(--orange)}
.caret{width:0;height:0;border-left:5px solid transparent;border-right:5px solid transparent;border-top:6px solid currentColor}

/* dropdown */
.dropdown{left:126px;top:134px;width:566px;height:157px;background:var(--panel);z-index:3;display:flex;padding:18px 8px 0}
.cap{width:92px;text-align:center;color:var(--white);font:500 12px "Montserrat",sans-serif;line-height:17px}
.cap-badge{display:block;width:68px;height:68px;margin:0 auto 14px;border-radius:50%}
.cap-badge.warm{background:radial-gradient(circle,#2a5688 55%,#c9822e 100%)}
.cap-badge.cool{background:radial-gradient(circle,#2a5688 55%,#c9d3e2 100%)}

/* login card */
.card{left:76px;top:210px;width:842px;height:532px;background:var(--card);border-radius:6px}
.card-title{left:0;width:994px;top:252px;text-align:center;font:700 28px "Montserrat",sans-serif;color:var(--navy)}
.field{left:191px;width:610px;height:52px;background:var(--white);border:2px solid #e3e5ef;border-radius:5px;display:flex;align-items:center;justify-content:space-between;padding:0 16px 0 18px;font:500 17px "Montserrat",sans-serif}
.remember{left:190px;top:455px;display:flex;align-items:center;gap:10px;font:500 14.5px "Montserrat",sans-serif}
.radio{width:24px;height:24px;border:1.5px solid #555;border-radius:50%;background:var(--white)}
.submit{left:388px;top:501px;width:218px;height:50px;background:var(--green);border-radius:3px;color:var(--white);font:700 18px "Montserrat",sans-serif;display:flex;align-items:center;justify-content:center}
.forgot{left:0;width:994px;top:600px;text-align:center;font:400 14px "Montserrat",sans-serif;color:var(--link)}
.forgot span{border-bottom:1px solid var(--link);padding-bottom:1px}
.sso{left:381px;top:674px;display:flex;align-items:center;gap:12px;font:500 14px "Montserrat",sans-serif}
.sso-dot{width:30px;height:30px;border-radius:50%;border:4px solid #4a85f0}

/* footer */
.footer{left:0;top:818px;width:994px;height:348px;background:linear-gradient(180deg,#245a8e 0%,#1c4a7b 55%,#123a66 100%)}
.footer-brand{left:0;width:994px;top:868px;display:flex;justify-content:center;align-items:center;gap:14px}
.footer-mark{width:52px;height:52px;border:3px solid var(--orange)}
.footer-name{font:700 31px "Roboto",sans-serif;color:var(--white)}
.col-head{top:965px;color:var(--white);font:700 12px "Montserrat",sans-serif;text-transform:uppercase}
.col-rule{top:990px;height:1px;background:rgba(255,255,255,.45)}
.f-text{color:var(--white);font:500 11.5px "Roboto Condensed",sans-serif;line-height:16px}
.f-icon{width:16px;height:16px;border:1.5px solid var(--white);border-radius:50%}
.f-social{width:20px;height:20px;border-radius:50%;background:rgba(255,255,255,.35)}
.news-input{left:649px;top:1048px;width:214px;height:26px;background:var(--white);border-radius:13px;font:500 11.5px "Montserrat",sans-serif;color:#333;padding:6px 0 0 17px}
.news-btn{left:649px;top:1083px;width:107px;height:25px;background:var(--orange);border-radius:13px;color:var(--white);font:700 10.5px "Montserrat",sans-serif;display:flex;align-items:center;justify-content:center}
.copyright{left:0;top:1166px;width:994px;height:34px;background:var(--orange);color:var(--white);font:700 9.5px "Montserrat",sans-serif;display:flex;align-items:center;justify-content:center}
</style>
</head>
<body>

<!-- top bar -->
<div class="abs topbar"></div>
<div class="abs topbar-item" style="left:625px">
  <span class="ring"><svg width="10" height="10" viewBox="0 0 10 10"><path d="M2 1l2 2-1 1c.5 1.2 1.5 2.3 3 3l1-1 2 2-1.5 1.5C4.5 9 1 5.5.5 2.5z" fill="#fff"/></svg></span>1800.555.0199
</div>
<div class="abs topbar-item" style="left:768px">
  <span class="ring"><svg width="10" height="8" viewBox="0 0 10 8"><rect x=".5" y=".5" width="9" height="7" fill="none" stroke="#fff"/><path d="M.5 .5l4.5 4 4.5-4" fill="none" stroke="#fff"/></svg></span>info@9lodgia.fr
</div>
<div class="abs social-dot" style="left:917px"></div>
<div class="abs social-dot" style="left:939px"></div>
<div class="abs social-dot" style="left:961px"></div>

<!-- header -->
<div class="abs brand"><span class="brand-mark"></span><span class="brand-name">9lodgia.Fr</span></div>
<div class="abs account" style="left:761px">
  <svg width="14" height="16" viewBox="0 0 14 16"><path d="M5 1v8l-2-1-1 1 4 6h6l1-6-4-1V1z" fill="var(--navy)"/></svg>Register
</div>
<div class="abs sep" style="left:842px"></div>
<div class="abs account" style="left:855px">
  <svg width="14" height="16" viewBox="0 0 14 16"><path d="M3 7V5a4 4 0 018 0v2" fill="none" stroke="var(--navy)" stroke-width="2"/><rect x="1" y="7" width="12" height="9" rx="1" fill="var(--navy)"/></svg>Login
</div>
<div class="abs sep" style="left:919px"></div>
<div class="abs account" style="left:932px">
  <span style="width:14px;height:14px;border-radius:50%;background:#c8102e;display:inline-block"></span>EN
  <svg width="10" height="6" viewBox="0 0 10 6"><path d="M1 1l4 4 4-4" fill="none" stroke="#1b1b1b" stroke-width="1.6"/></svg>
</div>

<!-- nav -->
<nav class="abs nav"></nav>
<div class="abs nav-item" style="left:63px">Home</div>
<div class="abs nav-item active" style="left:141px">Gîte par capacité <span class="caret"></span></div>
<div class="abs nav-item" style="left:297px">Gîte par département <span class="caret"></span></div>
<div class="abs nav-item" style="left:479px">Gîte par thématique <span class="caret"></span></div>
<div class="abs nav-item" style="left:652px">Blog</div>
<div class="abs nav-item" style="left:721px">Vos Favoris</div>
<div class="abs nav-item" style="left:835px">Contactez nous</div>
<svg class="abs" style="left:213px;top:124px;z-index:4" width="18" height="24" viewBox="0 0 18 24"><path d="M5 2a1.5 1.5 0 013 0v8l1-.5a1.5 1.5 0 013 0v1a1.5 1.5 0 013 .5v1a1.5 1.5 0 012.5 1V18c0 3-2 5-5 5H9c-2 0-3-1-4-2L1 15a1.5 1.5 0 012-2l2 2z" fill="#fff" stroke="#000" stroke-width="1"/></svg>

<!-- login card -->
<div class="abs card"></div>
<div class="abs card-title">Connexion</div>

<div class="abs dropdown">
  <div class="cap"><span class="cap-badge warm" role="img" aria-label="Pictogramme de capacité 2 à 20 personnes"></span>2 à 20<br>personnes</div>
  <div class="cap"><span class="cap-badge cool" role="img" aria-label="Pictogramme de capacité 20 à 40 personnes"></span>20 à 40<br>personnes</div>
  <div class="cap"><span class="cap-badge warm" role="img" aria-label="Pictogramme de capacité 40 à 60 personnes"></span>40 à 60<br>personnes</div>
  <div class="cap"><span class="cap-badge cool" role="img" aria-label="Pictogramme de capacité 60 à 80 personnes"></span>60 à 80<br>personnes</div>
  <div class="cap"><span class="cap-badge warm" role="img" aria-label="Pictogramme de capacité 80 à 120 personnes"></span>80 à 120<br>personnes</div>
  <div class="cap"><span class="cap-badge cool" role="img" aria-label="Pictogramme de capacité plus de 120 personnes"></span>+de 120<br>personnes</div>
</div>

<div class="abs field" style="top:326px"><span>Adresse email</span>
  <svg width="20" height="15" viewBox="0 0 20 15"><rect x="1" y="1" width="18" height="13" fill="none" stroke="#f7941d" stroke-width="1.5"/><path d="M1 1l9 7 9-7M1 14l7-6M19 14l-7-6" fill="none" stroke="#f7941d" stroke-width="1.5"/></svg>
</div>
<div class="abs field" style="top:391px"><span>Mot de passe</span>
  <svg width="18" height="24" viewBox="0 0 18 24"><path d="M4 11V7a5 5 0 0110 0v4" fill="none" stroke="#f7941d" stroke-width="2.5"/><rect x="1" y="10" width="16" height="13" rx="3" fill="#f7941d"/><rect x="8" y="14" width="2" height="5" fill="#fff"/></svg>
</div>
<div class="abs remember"><span class="radio"></span>Se souvenir de moi</div>
<div class="abs submit">Entrer</div>
<div class="abs forgot"><span>Avez-vous oublié votre mot de passe ?</span></div>
<div class="abs sso"><span class="sso-dot"></span>Se connecter ave Nuvio</div>

<!-- footer -->
<div class="abs footer" role="img" aria-label="Photo de Paris au crépuscule avec la tour Eiffel en fond, teintée de bleu"></div>
<div class="abs footer-brand"><span class="footer-mark"></span><span class="footer-name">9lodgia.Fr</span></div>

<div class="abs col-head" style="left:132px">Quick Links</div>
<div class="abs col-rule" style="left:132px;width:107px"></div>
<div class="abs f-text" style="left:132px;top:1006px">Gîte par capacité<br>Gîte par département<br>Gîte par thématique<br>Blog<br>Contactez nous</div>

<div class="abs col-head" style="left:310px">Contact</div>
<div class="abs col-rule" style="left:310px;width:117px"></div>
<div class="abs f-icon" style="left:308px;top:1009px"></div>
<div class="abs f-text" style="left:329px;top:1006px">9Lodgia.fr<br>123 Lorem Ipsum Dr<br>Paris, France</div>
<div class="abs f-icon" style="left:308px;top:1071px"></div>
<div class="abs f-text" style="left:329px;top:1070px">1800.555.0199</div>
<div class="abs f-icon" style="left:308px;top:1102px"></div>
<div class="abs f-text" style="left:329px;top:1101px">info@9lodgia.fr</div>

<div class="abs col-head" style="left:498px">Follow Us</div>
<div class="abs col-rule" style="left:498px;width:83px"></div>
<div class="abs f-social" style="left:498px;top:1007px"></div>
<div class="abs f-text" style="left:528px;top:1009px">pagelink</div>
<div class="abs f-social" style="left:498px;top:1038px"></div>
<div class="abs f-text" style="left:528px;top:1040px">chirpnet</div>
<div class="abs f-social" style="left:498px;top:1068px"></div>
<div class="abs f-text" style="left:528px;top:1070px">snapview</div>

<div class="abs col-head" style="left:651px">Newsletter</div>
<div class="abs col-rule" style="left:651px;width:213px"></div>
<div class="abs f-text" style="left:651px;top:1006px">Register your email address to get more<br>information about us and our services</div>
<div class="abs news-input">Email Address</div>
<div class="abs news-btn">SUBSCRIBE</div>

<div class="abs copyright">COPYRIGHT © 2019 9LODGIA.FR. ALL RIGHTS RESERVED.</div>

</body>
</html>
```